Design Cover for Catalog and theme pages to match cover design for continuity

I need a catalog cover for our new catalog and have it flow through the pages uniting the design together. Most the hardest work is complete however it needs a designers touch to bring it all together. The attached files include the catalog with products images data and logos. We have more assets however with the 100MB limit we are unable to upload to many more. For additional images you can pull them from our website www.brovantek.example.

Target Market(s)

Tradesmen and trades women who work in the Electrical and Industrial Automation spaces.

Industry/Entity Type

Industrial

Font styles to use
Sans Serif

Colors
3176b5
0555a3
85cae6

Requirements
Must have
• Complete cover design
• Must also have cover theme flow through remaining pages
Nice to have
• Header and Footer on each page
• Index on cover with page reference
Should not have
• This is not a redesign of the whole catalog, please don't drastically change the pages or any of the data in the tables.

```html
<!DOCTYPE html>
<html lang="en">
<head>
<meta charset="utf-8">
<title>Products Catalog 2017 – Enclosures &amp; LED Lighting</title>
<link href="https://fonts.googleapis.com/css2?family=Oswald:wght@400;500&family=Roboto+Condensed:wght@300;400&display=swap" rel="stylesheet">
<style>
  :root{
    --frame-blue:#3a6fb8;
    --brand-blue:#3176b5;
    --deep-blue:#0555a3;
    --sky-blue:#85cae6;
    --navy:#27408f;
    --ink:#1d1d1f;
    --rule:#9a9a9a;
    --head-gray:#8c8f93;
    --cell-gray:#d9dadc;
    --canvas:#e8ebef;
  }
  *{box-sizing:border-box;margin:0;padding:0}
  html,body{width:1200px;height:1200px;overflow:hidden;background:var(--canvas)}
  body{font-family:"Roboto Condensed",Arial,sans-serif;color:var(--ink)}
  .spread{position:absolute;left:20px;top:225px;width:1430px;height:925px;transform:scale(.811);transform-origin:0 0;background:#fff;box-shadow:0 4px 18px rgba(0,0,0,.18)}
  .frame{position:absolute;left:33px;top:31px;width:1363px;height:894px;background:var(--frame-blue)}
  .sheet{position:absolute;left:65px;top:63px;width:1300px;height:862px;background:#fff}
  .gutter{position:absolute;left:714px;top:0;width:1px;height:925px;background:rgba(0,0,0,.06)}
  .running-head{position:absolute;top:42px;left:273px;color:#fff;font-size:10px;letter-spacing:4px}
  .brand{position:absolute;top:37px;left:1025px;color:var(--sky-blue);font:500 15px "Oswald",sans-serif;display:flex;align-items:center;gap:4px}
  .brand i{display:inline-block;width:9px;height:9px;border-radius:50%;background:var(--sky-blue)}
  .abs{position:absolute}
  .section-mark{position:absolute;width:70px;height:70px;z-index:1}
  .section-mark::before{content:"";position:absolute;left:0;top:0;width:34px;height:66px;border-left:6px solid var(--navy);border-top:6px solid var(--navy)}
  .section-mark::after{content:"";position:absolute;left:7px;top:7px;width:64px;height:60px;border-left:6px solid var(--sky-blue);border-top:6px solid var(--sky-blue)}
  .section-title{position:absolute;z-index:3;font:500 22px/23px "Oswald",sans-serif;text-transform:uppercase;transform:scaleX(.78);transform-origin:0 0;color:#111;white-space:nowrap}
  .photo{position:absolute;border-radius:4px;z-index:0}
  .badge-row{position:absolute;display:flex;align-items:center;gap:10px;z-index:2}
  .badge{display:block;background:var(--deep-blue)}
  .badge.round{width:40px;height:40px;border-radius:50%}
  .badge.square{width:34px;height:34px;background:#222}
  .badge.hex{width:34px;height:34px;border-radius:50%;background:#f3c300}
  .cert-note{font-family:"Times New Roman",serif;font-size:13px}
  table.spec{position:absolute;z-index:2;background:#fff;border-collapse:collapse;font-size:8px;text-align:center}
  table.spec th,table.spec td{border:1px solid var(--rule);padding:0 3px;font-weight:300}
  table.spec th{background:var(--cell-gray);font-size:7.5px;line-height:9px}
  table.spec th.dark{background:var(--head-gray);color:#fff}
  table.spec th.blank{background:#fff;border:none}
  table.spec td.label{background:var(--cell-gray);text-align:left;padding-left:14px}
  table.spec td.left{text-align:left;padding-left:4px;line-height:11px}
  .rule-line{position:absolute;height:2px;background:#222}
  .rule-thin{position:absolute;height:1px;background:#777}
  .code{position:absolute;font-size:14px}
  .code-note{position:absolute;font-size:6px;text-align:center;line-height:15px}
  .cap{position:absolute;z-index:2;font-size:7px}
  .vert{writing-mode:vertical-rl;transform:rotate(180deg);font-size:8px}
  .edge-tab{position:absolute;background:var(--frame-blue)}
</style>
</head>
<body>
<div class="spread">
  <div class="frame"></div>
  <div class="sheet"></div>
  <div class="gutter"></div>
  <div class="edge-tab" style="left:1365px;top:540px;width:31px;height:90px"></div>
  <div class="edge-tab" style="left:1365px;top:828px;width:31px;height:97px"></div>

  <div class="running-head">PRODUCTS CATALOG 2017</div>
  <div class="brand">Brovantek <i></i></div>

  <!-- Ex-rated enclosures -->
  <div class="section-mark" style="left:83px;top:78px"></div>
  <div class="section-title" style="left:106px;top:102px">Ex-Rated Aluminum Enclosures</div>
  <div class="photo" role="img" aria-label="Group of open grey cast aluminum enclosures with clear lids" style="left:83px;top:138px;width:347px;height:122px;background:linear-gradient(135deg,#c9ccd0,#8e949a 60%,#b6bcc4)"></div>
  <div class="badge-row" style="left:193px;top:272px">
    <span class="badge square"></span><span class="badge round"></span><span class="badge hex"></span>
    <span class="cert-note">II 2 Gb Ex e II IP67</span>
  </div>
  <table class="spec" style="left:449px;top:76px;width:226px">
    <tr style="height:24px"><th>OUTSIDE DIM.<br>L x W x H</th><th>SHPG.<br>WEIGHT</th><th>MODEL NO.<br><span style="background:var(--head-gray);color:#fff;display:block">Gray Cast Aluminum</span></th></tr>
    <tr style="height:20.5px"><td>61 x 71 x 48</td><td>0.55 lbs</td><td>SG-AL-617148</td></tr>
    <tr style="height:20.5px"><td>93 x 70 x 52</td><td>0.59 lbs</td><td>SG-AL-937052</td></tr>
    <tr style="height:20.5px"><td>128 x 70 x 52</td><td>0.86 lbs</td><td>SG-AL-127052</td></tr>
    <tr style="height:20.5px"><td>110 x 110 x 52</td><td>1.03 lbs</td><td>SG-AL-111152</td></tr>
    <tr style="height:20.5px"><td>172 x 70 x 55</td><td>1.21 lbs</td><td>SG-AL-177055</td></tr>
    <tr style="height:20.5px"><td>145 x 125 x 62</td><td>1.29 lbs</td><td>SG-AL-121462</td></tr>
    <tr style="height:20.5px"><td>120 x 120 x 80</td><td>1.80 lbs</td><td>SG-AL-121208</td></tr>
    <tr style="height:20.5px"><td>235 x 80 x 80</td><td>2.23 lbs</td><td>SG-AL-238080</td></tr>
    <tr style="height:20.5px"><td>190 x 125 x 80</td><td>2.30 lbs</td><td>SG-AL-191208</td></tr>
    <tr style="height:20.5px"><td>160 x 160 x 90</td><td>2.56 lbs</td><td>SG-AL-161609</td></tr>
    <tr style="height:20.5px"><td>220 x 125 x 90</td><td>3.01 lbs</td><td>SG-AL-122209</td></tr>
    <tr style="height:20.5px"><td>260 x 160 x 90</td><td>3.32 lbs</td><td>SG-AL-162609</td></tr>
  </table>

  <!-- Hinge boxes -->
  <div class="section-mark" style="left:83px;top:352px"></div>
  <div class="rule-line" style="left:243px;top:361px;width:432px"></div>
  <div class="section-title" style="left:105px;top:376px">Aluminum Hinge<br>Boxes/Push<br>Button Hinge<br>Boxes</div>
  <div class="photo" role="img" aria-label="Grey aluminum hinge box with orange end caps, type A" style="left:235px;top:418px;width:125px;height:85px;background:linear-gradient(150deg,#cfd2d5,#9fa4a9 55%,#e08a3c)"></div>
  <div class="cap" style="left:312px;top:505px">*Type A</div>
  <div class="photo" role="img" aria-label="White hinge box with orange end caps, type B" style="left:383px;top:395px;width:175px;height:72px;background:linear-gradient(150deg,#f4f4f4,#dedede 60%,#e79a4a)"></div>
  <div class="cap" style="left:508px;top:440px">*Type B</div>
  <div class="badge-row" style="left:570px;top:378px"><span class="badge round"></span><span class="badge square"></span></div>

  <div class="code" style="left:395px;top:475px">HB</div>
  <div class="code" style="left:460px;top:475px">55</div>
  <div class="code" style="left:522px;top:475px">1000</div>
  <div class="code" style="left:580px;top:475px">A</div>
  <div class="rule-thin" style="left:428px;top:485px;width:10px"></div>
  <div class="rule-thin" style="left:495px;top:485px;width:10px"></div>
  <div class="rule-thin" style="left:400px;top:493px;width:18px"></div>
  <div class="rule-thin" style="left:458px;top:493px;width:18px"></div>
  <div class="rule-thin" style="left:525px;top:493px;width:24px"></div>
  <div class="rule-thin" style="left:576px;top:493px;width:18px"></div>
  <div class="rule-thin" style="left:408px;top:493px;width:1px;height:25px"></div>
  <div class="rule-thin" style="left:467px;top:493px;width:1px;height:25px"></div>
  <div class="rule-thin" style="left:537px;top:493px;width:1px;height:25px"></div>
  <div class="rule-thin" style="left:585px;top:493px;width:1px;height:25px"></div>
  <div class="code-note" style="left:385px;top:518px;width:45px">Hinge Box</div>
  <div class="code-note" style="left:442px;top:518px;width:50px">SIZE<br>50mm x 50mm<br>70mm x 50mm<br>70mm x 70mm<br>90mm x 90mm</div>
  <div class="code-note" style="left:505px;top:518px;width:65px;line-height:8px">Length(mm) No Holes<br><br>100-1000mm<br>In 50mm Increments</div>
  <div class="abs" style="left:576px;top:522px;width:18px;height:18px;border:1px solid #555"></div>
  <div class="code-note" style="left:572px;top:538px;width:26px">Type A</div>
  <div class="abs" style="left:576px;top:563px;width:18px;height:16px;border:1px solid #555;border-top:none;border-right:none"></div>
  <div class="code-note" style="left:572px;top:578px;width:26px">Type B</div>

  <table class="spec" style="left:84px;top:531px;width:273px">
    <tr style="height:15px"><th colspan="2" class="blank"></th><th colspan="2">MODEL NO.</th></tr>
    <tr style="height:16px"><th class="dark">SIZE</th><th class="dark">THICKNESS</th><th class="dark">Type A</th><th class="dark">Type B</th></tr>
    <tr style="height:24px"><td>50mm x 50mm</td><td>1.2mm</td><td>HB-55-1000A</td><td>HB-55-1000B</td></tr>
    <tr style="height:24px"><td>70mm x 50mm</td><td>1.2mm</td><td>HB-75-1000A</td><td>HB-75-1000B</td></tr>
    <tr style="height:24px"><td>70mm x 70mm</td><td>1.4mm</td><td>HB-77-1000A</td><td>HB-77-1000B</td></tr>
    <tr style="height:24px"><td>90mm x 90mm</td><td>1.6mm</td><td>HB-90-1000A</td><td>HB-90-1000B</td></tr>
  </table>

  <div class="photo" role="img" aria-label="Push button hinge boxes with red, green and amber buttons and an emergency stop" style="left:398px;top:600px;width:270px;height:150px;background:linear-gradient(135deg,#b9bec3,#e2823a 45%,#c9cdd1 75%,#f1f1f1)"></div>
  <div class="cap" style="left:468px;top:712px">*Type A</div>
  <div class="photo" role="img" aria-label="White push button boxes with orange caps and open hinge profile, type B" style="left:48px;top:695px;width:210px;height:140px;background:linear-gradient(135deg,#f1f1f1,#e88c3e 45%,#c9cbcd 70%,#f6f6f6)"></div>
  <div class="cap" style="left:143px;top:828px">*Type B</div>

  <table class="spec" style="left:266px;top:761px;width:421px">
    <tr style="height:12px"><th colspan="2" class="blank"></th><th colspan="6" class="dark">MODEL NUMBER</th></tr>
    <tr style="height:18px"><th colspan="2">HOLE SIZE</th><th>1 HOLE</th><th>2 HOLE</th><th>3 HOLE</th><th>4 HOLE</th><th>5 HOLE</th><th>6 HOLE</th></tr>
    <tr style="height:56px"><td style="width:14px"><span class="vert">Type A</span></td><td>22<br>25<br>30</td>
      <td class="left">HB-PB-2201A<br>HB-PB-2501A<br>HB-PB-3001A</td><td class="left">HB-PB-2202A<br>HB-PB-2502A<br>HB-PB-3002A</td><td class="left">HB-PB-2203A<br>HB-PB-2503A<br>HB-PB-3003A</td><td class="left">HB-PB-2204A<br>HB-PB-2504A<br>HB-PB-3004A</td><td class="left">HB-PB-2205A<br>HB-PB-2505A<br>HB-PB-3005A</td><td class="left">HB-PB-2206A<br>HB-PB-2506A<br>HB-PB-3006A</td></tr>
    <tr style="height:56px"><td><span class="vert">Type B</span></td><td>22<br>25<br>30</td>
      <td class="left">HB-PB-2201B<br>HB-PB-2501B<br>HB-PB-3001B</td><td class="left">HB-PB-2202B<br>HB-PB-2502B<br>HB-PB-3002B</td><td class="left">HB-PB-2203B<br>HB-PB-2503B<br>HB-PB-3003B</td><td class="left">HB-PB-2204B<br>HB-PB-2504B<br>HB-PB-3004B</td><td class="left">HB-PB-2205B<br>HB-PB-2505B<br>HB-PB-3005B</td><td class="left">HB-PB-2206B<br>HB-PB-2506B<br>HB-PB-3006B</td></tr>
  </table>

  <!-- LED machine light -->
  <div class="section-mark" style="left:750px;top:78px"></div>
  <div class="section-title" style="left:776px;top:103px">LED Machine Light</div>
  <div class="badge-row" style="left:1211px;top:78px"><span class="badge round" style="width:46px;height:46px"></span><span class="badge square"></span></div>
  <div class="photo" role="img" aria-label="LED machine light housing with cable, waterproof detail and angle bracket" style="left:763px;top:138px;width:310px;height:182px;background:linear-gradient(135deg,#eef2f6,#9aa6b6 45%,#4a6fb0 75%,#dfe3e8)"></div>
  <div class="cap" style="left:986px;top:206px;line-height:10px">Waterproof, Heat dissipation<br>Angle adjustment function</div>
  <div class="cap" style="left:950px;top:308px">Angle adjustment Function</div>
  <table class="spec" style="left:1096px;top:149px;width:236px">
    <tr style="height:22px"><td class="label">LED COLOR</td><td class="left">White</td></tr>
    <tr style="height:50px"><td class="label">CASE MATERIAL &amp; COLOR</td><td class="left">Body: Aluminum/Silver<br>Lens: Chemical Heat Strengthened Glass/Translucence<br>Cover: Die Casting/Dark Gray</td></tr>
    <tr style="height:22px"><td class="label">INPUT VOLTAGE</td><td class="left">AC110V / AC220V / DC24V</td></tr>
    <tr style="height:22px"><td class="label">COUNTRIES</td><td class="left">6W &nbsp;/&nbsp; 5.5W &nbsp;/&nbsp; 12W</td></tr>
    <tr style="height:24px"><td class="label">STANDARDS</td><td class="left">-20° ~ +40°</td></tr>
  </table>
  <table class="spec" style="left:749px;top:341px;width:303px">
    <tr style="height:20px"><th>MODEL</th><th>SIZE (MM)<br>L x H x W</th><th>BRIGHTNESS</th><th>WEIGHT</th></tr>
    <tr style="height:25px"><td>SG-LED-ML-146</td><td>146 x 65 x 50</td><td>165 lx</td><td>1.69 lbs</td></tr>
    <tr style="height:24px"><td>SG-LED-ML-280</td><td>280 x 65 x 50</td><td>280 lx</td><td>2.64 lbs</td></tr>
    <tr style="height:24px"><td>SG-LED-ML-414</td><td>414 x 65 x 50</td><td>460 lx</td><td>3.46 lbs</td></tr>
    <tr style="height:24px"><td>SG-LED-ML-548</td><td>548 x 65 x 50</td><td>615 lx</td><td>3.96 lbs</td></tr>
  </table>
  <div class="photo" role="img" aria-label="Four LED machine lights in increasing lengths" style="left:1068px;top:363px;width:290px;height:159px;background:linear-gradient(160deg,#fff 20%,#333 40%,#f5f5f5 55%,#2a2a2a 80%,#fff)"></div>

  <!-- Aluminum profile LED lamp -->
  <div class="rule-thin" style="left:848px;top:555px;width:500px"></div>
  <div class="section-mark" style="left:750px;top:545px"></div>
  <div class="section-title" style="left:776px;top:570px">Aluminum<br>Profile<br>LED Lamp</div>
  <div class="badge-row" style="left:1243px;top:572px"><span class="badge round" style="width:46px;height:46px"></span><span class="badge square"></span></div>
  <div class="photo" role="img" aria-label="Black aluminum profile LED lamps in three lengths" style="left:736px;top:650px;width:320px;height:150px;background:linear-gradient(155deg,#fff 10%,#2b2b2b 40%,#6c6c6c 55%,#1f1f1f 75%,#fff)"></div>
  <div class="photo" role="img" aria-label="Fixed mounting bracket and inline switch" style="left:1068px;top:605px;width:105px;height:175px;background:linear-gradient(180deg,#2a2a2a,#8a8a8a 50%,#1e1e1e)"></div>
  <div class="cap" style="left:1082px;top:683px;color:#fff">*Fixed Bracket</div>
  <div class="cap" style="left:1100px;top:784px">*Switch</div>
  <table class="spec" style="left:1206px;top:632px;width:192px">
    <tr style="height:22px"><th>LENGTH<br>(mm)</th><th>WEIGHT<br>(lb)</th><th>MOUNTING<br>BRACKETS</th><th>MODEL NO.</th></tr>
    <tr style="height:21.5px"><td>152</td><td>0.26</td><td>2</td><td>SG-LED1C-02</td></tr>
    <tr style="height:21.5px"><td>292</td><td>0.53</td><td>2</td><td>SG-LED1C-03</td></tr>
    <tr style="height:21.5px"><td>444</td><td>0.72</td><td>2</td><td>SG-LED1C-04</td></tr>
    <tr style="height:21.5px"><td>584</td><td>0.91</td><td>3</td><td>SG-LED1C-05</td></tr>
    <tr style="height:21.5px"><td>736</td><td>1.14</td><td>3</td><td>SG-LED1C-06</td></tr>
    <tr style="height:21.5px"><td>876</td><td>1.24</td><td>3</td><td>SG-LED1C-07</td></tr>
    <tr style="height:21.5px"><td>1041</td><td>1.56</td><td>4</td><td>SG-LED1C-08</td></tr>
  </table>
  <table class="spec" style="left:801px;top:834px;width:501px">
    <tr style="height:22px"><th>LED COLOR</th><th>CASE COLOR</th><th>BRIGHTNESS</th><th>INPUT VOLTAGE</th><th>POWER<br>COMSUPTION</th><th>OPERATING<br>TEMPERATURE</th><th>GREEN<br>PRODUCTS</th></tr>
    <tr style="height:36px"><td>White</td><td>Black</td><td>1m:63lux, 0.5m:190lux</td><td>AC110V</td><td>Below 3.5W</td><td>-10°C ~ 60°C</td><td>RoHS, Pb free</td></tr>
  </table>
</div>
</body>
</html>
```